Upmarket Dessert Lounge needs a Business Card Design

We are an upmarket dessert lounge needing a business card to match our image.

We want something that is simple yet beautiful, feminine, classy, sophisticated and elegant. We want it to stand out and don't mind if it is bold.

The design should include our logo and colours of red or maroon with gold highlights. We don't mind if black is used.

Marlow & Quince

Target Market(s)

For those who like to indulge or treat themselves and give in to their temptations on good quality desserts.

Industry/Entity Type

Business

Requirements
Must have
• Must include our logo and our name

Marlow & Quince

M & Q

```html
<!DOCTYPE html>
<html lang="en">
<head>
<meta charset="utf-8">
<title>Marlow &amp; Quince — Business Card</title>
<link rel="stylesheet" href="https://fonts.googleapis.com/css2?family=Libre+Baskerville:wght@400;700&family=PT+Sans:wght@400&display=swap">
<style>
  :root {
    --backdrop: #e9e4de;
    --card-black: #0b0908;
    --maroon: #7b1a1c;
    --cream: #f8cf98;
    --gold-cream: #f3d3a3;
    --ink: #1a1410;
    --white: #ffffff;
  }
  * { margin: 0; padding: 0; box-sizing: border-box; }
  html, body {
    width: 1200px; height: 758px; overflow: hidden;
    background: var(--backdrop);
  }
  .canvas { position: relative; width: 1200px; height: 758px; }

  .card {
    position: absolute;
    width: 520px; height: 300px;
    background: var(--card-black);
    border-radius: 28px;
    overflow: hidden;
    box-shadow: 0 10px 24px rgba(0,0,0,.25);
  }
  .card-front { left: 60px; top: 90px; }
  .card-back  { left: 620px; top: 360px; }

  /* Front */
  .front-brand {
    position: absolute; left: 18px; top: 138px; width: 230px;
    display: flex; align-items: center; justify-content: center; gap: 8px;
  }
  .brand-mark {
    width: 10px; height: 10px; background: var(--maroon); flex: none;
  }
  .brand-name {
    font-family: "Libre Baskerville", serif; font-weight: 400;
    font-size: 15px; color: var(--gold-cream); letter-spacing: .5px;
    text-transform: uppercase; white-space: nowrap;
  }
  .url-strip {
    position: absolute; left: 262px; top: 48px; width: 24px; height: 200px;
    background: var(--maroon);
    display: flex; align-items: center; justify-content: center;
  }
  .url-strip span {
    transform: rotate(-90deg); white-space: nowrap;
    font-family: "PT Sans", sans-serif; font-size: 12px; color: var(--white);
    letter-spacing: .5px;
  }
  .contact-panel {
    position: absolute; left: 290px; top: 48px; right: 0; height: 200px;
    background: var(--cream); padding: 20px 0 0 18px; color: var(--ink);
    font-family: "PT Sans", sans-serif;
  }
  .person-name {
    font-family: "Libre Baskerville", serif; font-weight: 700; font-size: 17px;
  }
  .person-title { font-size: 13px; margin-top: 6px; }
  .contact-list { list-style: none; margin-top: 18px; font-size: 13px; line-height: 17px; }
  .contact-list li { display: flex; align-items: center; gap: 5px; }
  .contact-list svg { width: 10px; height: 10px; flex: none; }
  .address { font-size: 13px; line-height: 17px; margin-top: 14px; padding-left: 15px; }

  /* Back */
  .back-monogram {
    position: absolute; left: 0; right: 0; top: 70px;
    display: flex; align-items: center; justify-content: center; gap: 14px;
  }
  .monogram-text {
    font-family: "Libre Baskerville", serif; font-weight: 400;
    font-size: 64px; color: var(--gold-cream); letter-spacing: 2px;
  }
  .monogram-mark { width: 16px; height: 16px; background: var(--maroon); }
  .back-url {
    position: absolute; left: 0; right: 0; top: 226px; text-align: center;
    font-family: "PT Sans", sans-serif; font-size: 22px; color: var(--white);
    letter-spacing: 2.5px;
  }
</style>
</head>
<body>
<main class="canvas">

  <section class="card card-front" aria-label="Business card front">
    <div class="front-brand">
      <span class="brand-mark"></span>
      <span class="brand-name">Marlow &amp; Quince</span>
    </div>

    <div class="url-strip"><span>www.marlowquince.com</span></div>

    <div class="contact-panel">
      <p class="person-name">Your name</p>
      <p class="person-title">Title</p>
      <ul class="contact-list">
        <li>
          <svg viewBox="0 0 10 10" aria-hidden="true"><circle cx="5" cy="5" r="4.3" fill="none" stroke="#1a1410" stroke-width="1"/><path d="M3.3 2.8c0 2.2 1.7 4.2 3.6 4.2l.3-1-1-.5-.5.5c-.8-.4-1.4-1.1-1.7-1.9l.5-.5-.4-1z" fill="#1a1410"/></svg>
          555-014-2368
        </li>
        <li>
          <svg viewBox="0 0 10 10" aria-hidden="true"><rect x="2.6" y="0.5" width="4.8" height="9" rx="1" fill="#1a1410"/><rect x="3.4" y="1.6" width="3.2" height="4.4" fill="#f8cf98"/></svg>
          555-014-2368
        </li>
        <li>
          <svg viewBox="0 0 10 10" aria-hidden="true"><rect x="0.5" y="2" width="9" height="6" fill="#1a1410"/><path d="M0.8 2.3 5 5.5 9.2 2.3" fill="none" stroke="#f8cf98" stroke-width=".8"/></svg>
          info@marlowquince.com
        </li>
      </ul>
      <p class="address">Street Name, City Name<br>State Zip Code</p>
    </div>
  </section>

  <section class="card card-back" aria-label="Business card back">
    <div class="back-monogram">
      <span class="monogram-mark"></span>
      <span class="monogram-text">M &amp; Q</span>
    </div>
    <p class="back-url">www.marlowquince.com</p>
  </section>

</main>
</body>
</html>
```